Re designing of website of VELTRIS Pens, an International stationary brand

We would like to re design our existing website veltrispens.com. We are leading manufacturers and exporters of stationary products. Our existence is global -selling and marketing in all 5 continents.

We are a 35year old group with focus on high quality, innovative designs and state of art manufacturing setup.

Client satisfaction by committed service and trust are the roots of our organisation.

We would like to see a website which focuses on our brand Veltris and must have an international appeal. Our target buyers would be Agents, distributors and wholesalers in various countries. Content would be similar to our existing website but designing and outlook needs to be totally different.

For the outlook we do like the following websites from our industry which can be used to draw inspiration.
1. www.duniverastationery.com
2. www.quorlapen.com
3. www.haltmivopen.com

The homepage need not be focused on the product but must emphasis on the branding of Veltris, our existence of 35years along with international presence and quality standards maintained by our organisation.
Updates

Reason: Would like to see some more concepts and designs as per artwork attached.

Target Market(s)

Wholesalers, Agents and Distributors in all countries around the world. Target market is global

Number of Pages Required

1 page

Font styles to use
Sans Serif

Requirements
Must have
• Focus on Branding, High Quality Standards, Customer Loyalty
Nice to have
• Like the outlook of the websites
• www.haltmivopen.com
• www.duniverastationery.com
• www.quorlapen.com
Should not have
• Don't like the outlook of our present website www.veltrispens.com
• It doesn't justify our brand or our product

```html
<!DOCTYPE html>
<html lang="en">
<head>
<meta charset="utf-8">
<title>VELTRIS Pens — World Class Writing Instruments</title>
<link rel="stylesheet" href="https://fonts.googleapis.com/css2?family=Source+Sans+3:wght@300;400;600;700&family=Open+Sans:wght@400;600;700&family=Oswald:wght@400&display=swap">
<style>
:root{
  --red:#ed1c24;
  --red-dark:#d4151c;
  --ink:#333333;
  --text:#444444;
  --muted:#9a9a9a;
  --white:#ffffff;
  --black:#000000;
  --line:#e2e2e2;
  --amber:#f1a90b;
}
*{margin:0;padding:0;box-sizing:border-box}
html,body{width:849px;height:1200px;overflow:hidden;background:var(--white)}
.page{position:relative;width:990px;height:1400px;transform:scale(0.857576);transform-origin:0 0;font-family:"Open Sans",sans-serif;color:var(--text)}
.abs{position:absolute}
.page span,.page a,.page h1,.page h2,.page h3,.page li{white-space:nowrap}

/* header */
.site-header{left:0;top:0;width:990px;height:84px;background:var(--red)}
.brand{left:78px;top:20px;display:flex;align-items:center;gap:5px}
.brand-square{width:38px;height:40px;background:var(--white)}
.brand-name{font-family:"Source Sans 3",sans-serif;font-weight:400;font-size:34px;color:var(--white);line-height:1;margin-top:-14px}
.brand-tag{left:121px;top:50px;font-family:"Source Sans 3",sans-serif;font-size:11px;font-weight:600;color:var(--white);white-space:nowrap}
.nav-item{position:absolute;top:0;height:84px;line-height:84px;font-family:"Source Sans 3",sans-serif;font-weight:600;font-size:12px;color:var(--white);text-decoration:none}
.nav-item.active{left:291px;width:49px;background:var(--red-dark);text-align:center;font-weight:700}
.search-icon{left:906px;top:37px}

/* hero */
.hero{left:0;top:84px;width:990px;height:411px;background:linear-gradient(90deg,#f6f6f6 0%,#efefef 55%,#f8f8f8 100%)}
.hero-art{left:60px;top:95px;width:340px;height:385px;border-radius:50%;background:radial-gradient(circle at 50% 45%,#dedede 0%,#e9e9e9 35%,#f3f3f3 70%,rgba(243,243,243,0) 100%)}
.hero-title{left:414px;top:141px;font-family:"Source Sans 3",sans-serif;font-weight:300;font-size:62px;line-height:54px;color:var(--red);letter-spacing:1px;white-space:nowrap}
.hero-copy{left:417px;top:265px;font-size:13px;line-height:18px;letter-spacing:1px;color:#222;white-space:nowrap}
.hero-copy strong{font-weight:700}
.btn-red{background:var(--red);color:var(--white);font-family:"Open Sans",sans-serif;font-weight:700;font-size:11px;display:flex;align-items:center;justify-content:center;box-shadow:0 2px 0 #b5121a}
.hero-btn{left:417px;top:347px;width:164px;height:36px}
.dots{left:417px;top:427px;display:flex;gap:7px}
.dots span{width:12px;height:12px;border:1px solid #666;border-radius:50%}
.dots .on{border:2px solid var(--red)}

/* welcome */
.section-title{font-family:"Source Sans 3",sans-serif;font-weight:400;font-size:26px;letter-spacing:1px;color:var(--ink);white-space:nowrap}
.section-title em{font-style:normal;color:var(--red)}
.welcome-title{left:72px;top:538px}
.welcome-copy{left:72px;top:587px;width:440px;font-size:10.5px;line-height:19px;color:#333}
.welcome-copy p+p{margin-top:6px}
.divider-v{left:529px;top:545px;width:1px;height:212px;background:var(--line)}

/* events */
.events-title{left:552px;top:538px}
.arrow-btn{width:25px;height:25px;border:1px solid #ccc;border-radius:50%;display:flex;align-items:center;justify-content:center}
.sort-label{left:862px;top:575px;font-size:8px;font-style:italic;color:#666}
.month{left:554px;top:583px;font-family:"Oswald",sans-serif;font-size:18px;color:#bdbdbd}
.filters{left:717px;top:592px;display:flex;align-items:center;gap:6px;font-size:7.5px;color:#aaa}
.filters .val{color:#555}
.filters .chip{background:#bbb;color:var(--white);font-style:italic;padding:1px 4px}
.filters .sep{width:1px;height:12px;background:#ccc;margin:0 3px}
.event-list{left:553px;top:619px;width:366px;height:116px;border:1px solid var(--line)}
.event{position:absolute;left:0;width:365px;height:57px;border-left:3px solid var(--red)}
.event.first{top:0;border-left-color:var(--amber);border-bottom:1px solid var(--line)}
.event.second{top:57px}
.ev-day{position:absolute;left:12px;font-family:"Oswald",sans-serif;color:#999}
.ev-day .dow{font-size:6px;display:block}
.ev-day .num{font-size:22px;line-height:20px;display:block}
.ev-day .mon{font-size:7px;display:block}
.ev-name{position:absolute;left:63px;top:10px;font-family:"Oswald",sans-serif;font-size:14px;color:#555}
.ev-meta{position:absolute;left:63px;top:31px;font-size:7.5px;font-style:italic;color:#aaa;line-height:10px;white-space:nowrap}
.ev-meta b{font-weight:400;color:#556}

/* countries */
.countries{left:0;top:809px;width:990px;height:230px;background:var(--red);color:var(--white)}
.countries-title{position:absolute;left:0;top:34px;width:990px;text-align:center;font-family:"Source Sans 3",sans-serif;font-weight:400;font-size:25px;letter-spacing:1px}
.countries-rule{position:absolute;left:71px;top:75px;width:848px;height:1px;background:rgba(255,255,255,0.55)}
.cloud{position:absolute;left:71px;top:88px;width:848px;font-family:"Source Sans 3",sans-serif;font-weight:600}
.cloud div{display:flex;justify-content:center;align-items:baseline;gap:14px;height:21.5px;white-space:nowrap}
.cloud span{font-size:10.5px}
.cloud .big{font-size:17px}

/* footer */
.footer{left:0;top:1039px;width:990px;height:361px;background:var(--black);color:var(--white)}
.fcol{position:absolute;top:52px;width:203px}
.fcol h3{font-family:"Open Sans",sans-serif;font-weight:600;font-size:13px;height:29px}
.fcol .rule{height:4px;border-bottom:1px solid #555;position:relative;margin-bottom:14px}
.fcol .rule::before{content:"";position:absolute;left:0;top:0;width:50px;height:4px;background:#ccc}
.fcol.news .rule::before{width:140px}
.fcol ul{list-style:none;font-size:10px;line-height:19px;color:#ddd}
.news p{font-size:11px;line-height:15px;color:#ddd}
.email{position:absolute;top:134px;left:0;width:202px;height:32px;background:var(--white);color:#888;font-size:10px;padding:10px 14px}
.subscribe{position:absolute;top:178px;left:0;width:116px;height:28px;gap:6px;font-weight:600;font-size:10px}
.footer-rule{position:absolute;left:71px;top:264px;width:848px;height:1px;background:#333}
.foot-brand{position:absolute;left:73px;top:290px;display:flex;align-items:center;gap:5px}
.foot-brand .brand-square{width:36px;height:40px;background:#666}
.foot-brand .brand-name{color:#888}
.foot-tag{position:absolute;left:117px;top:320px;font-family:"Source Sans 3",sans-serif;font-size:11px;font-weight:600;color:#888;white-space:nowrap}
.copyright{position:absolute;left:314px;top:306px;font-size:10px;color:#aaa;white-space:nowrap}
.social{position:absolute;left:786px;top:301px;display:flex;gap:6px}
.social span{width:22px;height:22px;border-radius:50%;background:#666}
.social .on{background:#3b5ba5}
</style>
</head>
<body>
<div class="page">

  <header class="site-header abs">
    <div class="brand abs"><span class="brand-square"></span><span class="brand-name">VELTRIS</span></div>
    <div class="brand-tag abs">World Class Writing Instruments</div>
    <a class="nav-item active" href="#">HOME</a>
    <a class="nav-item" href="#" style="left:354px">ABOUT US</a>
    <a class="nav-item" href="#" style="left:428px">PRODUCTS</a>
    <a class="nav-item" href="#" style="left:519px">PROMOTIONAL PRODUCTS</a>
    <a class="nav-item" href="#" style="left:673px">CAREERS</a>
    <a class="nav-item" href="#" style="left:741px">ENQUIRY FORM</a>
    <a class="nav-item" href="#" style="left:840px">CONTACT</a>
    <svg class="search-icon abs" width="13" height="13" viewBox="0 0 13 13"><circle cx="5.5" cy="5.5" r="4.3" fill="none" stroke="#fff" stroke-width="1.5"/><line x1="8.6" y1="8.6" x2="12" y2="12" stroke="#fff" stroke-width="1.5"/></svg>
  </header>

  <section class="hero abs"></section>
  <div class="hero-art abs" role="img" aria-label="Blue metal ballpoint pen with black grip standing upright"></div>
  <h1 class="hero-title abs">VELTRIS METAL<br>PENS</h1>
  <div class="hero-copy abs">
    We are leading manufacturers and exporters of stationary products.<br>
    Our existence is global<br>
    <strong>Selling and marketing in all 5 continents</strong>
  </div>
  <a class="btn-red hero-btn abs">CONTACT US</a>
  <div class="dots abs"><span></span><span></span><span class="on"></span><span></span></div>

  <h2 class="section-title welcome-title abs">WELCOME TO <em>VELTRIS</em></h2>
  <div class="welcome-copy abs">
    <p>Duis autem vel eum iriure dolor in hendrerit in vulputate velit esse molestie consequat, vel illum dolore eu feugiat nulla facilisis at vero eros et accumsan et iusto odio dignissim qui blandit praesent luptatum zzril delenit augue duis dolore te feugait nulla facilisi.</p>
    <p>Lorem ipsum dolor sit amet, consectetuer adipiscing elit, sed diam nonummy nibh euismod tincidunt ut laoreet dolore magna aliquam erat volutpat. Ut wisi enim ad minim veniam, quis nostrud exerci tation ullamcorper suscipit lobortis nisl ut aliquip ex ea commodo consequat. Duis autem vel eum iriure dolor in hendrerit in vulputate velit esse molestie consequat, vel illum dolore eu feugiat nulla facilisis at vero eros et accumsan et iusto odio dignissim qui blandit praesent luptatum zzril delenit augue duis dolore te feugait nulla facilisi.</p>
  </div>
  <div class="divider-v abs"></div>

  <h2 class="section-title events-title abs">EVENTS</h2>
  <div class="arrow-btn abs" style="left:863px;top:539px"><svg width="8" height="10" viewBox="0 0 8 10"><polyline points="6,1 2,5 6,9" fill="none" stroke="#bbb" stroke-width="1.3"/></svg></div>
  <div class="arrow-btn abs" style="left:894px;top:539px"><svg width="8" height="10" viewBox="0 0 8 10"><polyline points="2,1 6,5 2,9" fill="none" stroke="#bbb" stroke-width="1.3"/></svg></div>
  <div class="sort-label abs">SORT OPTIONS</div>
  <div class="month abs">JUNE, 2014</div>
  <div class="filters abs">
    <span>SORT BY:</span><span class="val">DATE ▾</span><span class="sep"></span>
    <span class="val">COUNTRY:</span><span class="chip">ALL</span>
    <span class="val" style="margin-left:8px">CITY:</span><span class="chip">ALL</span>
  </div>
  <div class="event-list abs">
    <div class="event first">
      <div class="ev-day" style="top:9px"><span class="dow">FRI</span><span class="num">20 <small style="font-size:9px">- 15</small></span><span class="mon">JUN</span></div>
      <div class="ev-name">CAMPING TRIP</div>
      <div class="ev-meta">◷ 8:00 am - (July 15) 5:00 am</div>
    </div>
    <div class="event second">
      <div class="ev-day" style="top:5px"><span class="dow">THU</span><span class="num">26</span><span class="mon">JUN</span></div>
      <div class="ev-name" style="top:5px">CINCO DE MAYO</div>
      <div class="ev-meta" style="top:24px">◷ 10:00 am - 3:00 pm &nbsp;⚲ 48 Linden Row, Marlow Bay 20418<br>Event Organized By: <b>Harbor Community Guild</b></div>
    </div>
  </div>

  <section class="countries abs">
    <h2 class="countries-title">EXPORTING COUNTRIES</h2>
    <div class="countries-rule"></div>
    <div class="cloud">
      <div><span class="big">ARGENTINA</span><span>ARMENIA</span><span>ARUBA</span><span>AUSTRALIA</span><span class="big">AUSTRIA</span><span>AZERBAIJAN</span><span class="big">BAHAMAS, THE BAHRAIN</span><span style="margin-left:20px">BANGLADESH</span><span class="big">BARBADOS</span></div>
      <div><span>BELARUS</span><span>BELGIUM</span><span>BELIZE</span><span>BENIN</span><span>BHUTAN</span><span>BOLIVIA</span><span>BOSNIA AND HERZEGOVINA</span><span class="big">BOTSWANA</span><span>BRAZIL</span><span>BRUNEI</span><span class="big">BULGARIA</span><span>BURKINA</span></div>
      <div><span>CAMEROON</span><span class="big">CANADA</span><span>CAPE VERDE</span><span>CENTRAL AFRICAN REPUBLIC</span><span class="big">CHAD</span><span class="big">CHILE</span><span>CHINA</span><span>COLOMBIA</span><span>COMOROS</span><span>CONGO, DEMOCRATIC REPUBLIC</span></div>
      <div><span>OF THE EGYPT</span><span>FRANCE</span><span>GEORGIA</span><span class="big">GERMANY</span><span>GHANA</span><span>HAITI</span><span>HONG KONG</span><span>HUNGARY</span><span class="big">INDIA</span><span>INDONESIA</span><span class="big">IRAN</span><span>IRAQ</span><span>IRELAND</span><span>ITALY</span></div>
      <div><span class="big">JAMAICA</span><span>JAPAN</span><span class="big">JORDAN</span></div>
    </div>
  </section>

  <footer class="footer abs">
    <div class="fcol" style="left:72px">
      <h3>PRODUCTS</h3><div class="rule"></div>
      <ul><li>Retail Products</li><li>Promotional Products</li></ul>
    </div>
    <div class="fcol" style="left:286px">
      <h3>INFORMATION</h3><div class="rule"></div>
      <ul><li>Order Now!</li><li>Privacy Policy</li><li>Payment Methods</li></ul>
    </div>
    <div class="fcol" style="left:501px">
      <h3>SUPPORT</h3><div class="rule"></div>
      <ul><li>Contact Us</li><li>Our Company</li><li>Veltris on Socialine</li></ul>
    </div>
    <div class="fcol news" style="left:716px">
      <h3>NEWSLETTER SUBSCRIPTION</h3><div class="rule"></div>
      <p>Subscribe for our Newsletter and Get latest Updates ....</p>
      <div class="email">Email</div>
      <a class="btn-red subscribe">
        <svg width="11" height="9" viewBox="0 0 11 9"><line x1="0" y1="4.5" x2="10" y2="4.5" stroke="#fff" stroke-width="1.3"/><polyline points="6,0.8 10,4.5 6,8.2" fill="none" stroke="#fff" stroke-width="1.3"/></svg>
        SUBSCRIBE
      </a>
    </div>
    <div class="footer-rule"></div>
    <div class="foot-brand"><span class="brand-square"></span><span class="brand-name">VELTRIS</span></div>
    <div class="foot-tag">World Class Writing Instruments</div>
    <div class="copyright">VELTRIS INC. PTY LTD © 2015.</div>
    <div class="social"><span></span><span class="on"></span><span></span><span></span><span></span></div>
  </footer>

</div>
</body>
</html>
```